Photographer's price list

I am a photographer who runs a studio (Marrowfield Studio) and need to have a document to send clients detailing my packages (collections) and prices. I have written the text in a word document and need a designer to lay it out for me using my logo and two specific fonts: DejaVu Sans and LainieDaySH.

The look should be clean and modern and keep in the same style as my logo. I will primarily be using the final product as a PDF file to email to potential clients. It should stay black and white.

I would also like to be able to update the text myself as my prices and packages change. So I would like a PSD file.

I think I would like for the document to be in landscape format with "Collections" on one side and A la Carte on the other, but I am open to other ideas.

As for sizing, it should be a standard size so that clients can print it out if they like.

Industry/Entity Type

Landscape

Requirements
Must have
• my logo
fonts: DejaVu and LainieDaySH
Easy to email
Easy to display on one page upon opening
Standard size so that printing from a home computer is easy to do.

```html
<!DOCTYPE html>
<html lang="en">
<head>
<meta charset="utf-8">
<title>Marrowfield Studio – 2013 Photography Collections</title>
<link href="https://fonts.googleapis.com/css2?family=Oswald:wght@300;400&family=Roboto+Condensed:wght@300;400&display=swap" rel="stylesheet">
<style>
:root{
  --paper:#ffffff;
  --backdrop:#e6e6e4;
  --ink:#3a3a3a;
  --ink-soft:#555555;
  --heading:#4a4a4a;
  --muted:#9a9a9a;
  --band:#a9a9a9;
  --rule:#cfcfcf;
  --ghost:#e8e8e8;
  --brand:#222222;
  --photo-a:#2c2c2c;
  --photo-b:#9c9c9c;
}
*{margin:0;padding:0;box-sizing:border-box}
html,body{width:1200px;height:849px;overflow:hidden;background:var(--backdrop)}
body{position:relative;font-family:"Roboto Condensed",sans-serif;color:var(--ink)}
.spread{position:absolute;width:1030px;height:364px;background:var(--paper);box-shadow:0 2px 6px rgba(0,0,0,.18)}
.spread--outer{left:75px;top:18px}
.spread--inner{left:85px;top:445px}
.page{position:absolute;top:0;width:515px;height:364px;overflow:hidden}
.page--left{left:0}
.page--right{left:515px}
.abs{position:absolute}
.band{position:absolute;left:0;background:var(--band)}
.heading{font-family:"Oswald",sans-serif;font-weight:300;color:var(--heading);text-transform:uppercase;line-height:1.15}
.body{font-size:6.3px;line-height:9px;color:var(--ink-soft);font-weight:300}
.photo{position:absolute;background:linear-gradient(135deg,var(--photo-b),var(--photo-a))}
.brand{position:absolute;display:flex;align-items:center;gap:7px;font-family:"Roboto Condensed",sans-serif;font-weight:400;color:var(--brand);letter-spacing:1.5px;white-space:nowrap}
.brand__mark{width:8px;height:8px;background:var(--brand)}

/* back page */
.about{left:43px;top:38px;width:350px}
.about .heading{font-size:16px;margin-bottom:5px}
.about p{margin-bottom:9px}
.about .sign{margin-left:4px}
.brand--back{left:70px;top:277px;font-size:11px}
.web{left:210px;top:296px;font-size:7px;letter-spacing:2px;color:var(--ink-soft);font-weight:400}

/* cover page */
.cover-photo{left:0;top:0;width:515px;height:183px}
.cover-band{top:183px;width:515px;height:7px}
.brand--cover{left:70px;top:271px;font-size:9.5px}
.cover-title{left:203px;top:271px;font-size:17px;letter-spacing:2px;color:var(--muted);white-space:nowrap}
.cover-call{left:243px;top:322px;font-size:16px;letter-spacing:2px;color:var(--muted);white-space:nowrap}

/* inner page 1 */
.ghost-name{left:78px;top:135px;font-family:"Roboto Condensed",sans-serif;font-size:26px;letter-spacing:4px;color:var(--ghost);white-space:nowrap}
.session{left:32px;top:14px;width:430px;font-size:16px}
.intro{left:32px;top:88px;width:220px}
.c-title{font-size:15px}
.col1{left:32px;top:157px;width:220px}
.col2{left:32px;top:235px;width:220px}
.col1 .body,.col2 .body{margin-top:8px}
.inner-photo{left:258px;top:168px;width:257px;height:188px}
.inner-band{top:356px;width:515px;height:8px}
.divider{left:515px;top:2px;width:1px;height:172px;background:var(--rule)}

/* inner page 2 */
.colA{left:37px;width:212px}
.colB{left:265px;width:215px}
.colA .body,.colB .body{margin-top:4px}
.item-title{font-size:12px}
.c3{top:24px}.c4{top:103px}
.alc{top:209px}
.alc-digital{top:278px}
.b1{top:27px}.b2{top:86px}.b3{top:133px}.b4{top:185px}.b5{top:238px}
</style>
</head>
<body>

<section class="spread spread--outer">
  <article class="page page--left back-page">
    <div class="abs about">
      <h2 class="heading">About us</h2>
      <p class="body">Marrowfield Studio, based in Rosenheim, Germany, is a newly launched studio led by American photographer, Clara Wendt Marrowfield. She specializes in portrait, children and cause-related photography, and is currently working on a collection featuring mothers and children.</p>
      <p class="body">Clara holds a Master's in Foreign Service and International Development from Halvorsen University, and a BA from Ridgeway College. She is available for assignments worldwide</p>
      <p class="body sign">CLARA Wendt<br>Rosenheim, 83022, Germany</p>
    </div>
    <div class="brand brand--back"><span class="brand__mark"></span><span>MARROWFIELD</span></div>
    <div class="abs web">www.marrowfieldstudio.com</div>
    <div class="band" style="top:355px;width:515px;height:9px"></div>
  </article>

  <article class="page page--right cover-page">
    <div class="photo cover-photo" role="img" aria-label="Black and white portrait of three children lying side by side, chins resting on their hands"></div>
    <div class="band cover-band"></div>
    <div class="brand brand--cover"><span class="brand__mark"></span><span>MARROWFIELD</span></div>
    <div class="abs heading cover-title">2013 Photography Collections</div>
    <div class="abs heading cover-call">Call now: 0401 552 718</div>
  </article>
</section>

<section class="spread spread--inner">
  <article class="page page--left inner-one">
    <div class="abs ghost-name" aria-hidden="true">MARROWFIELD</div>
    <h2 class="abs heading session">One to two hour portrait session with photographer in location of your choice (unlimited time if necessary!)</h2>
    <p class="abs body intro">Clara will create a presentation video with hand-selected music and custom editing, which tells your story, highlights the best images, and reveals the connections within your family. An online gallery for viewing and ordering helps you share your images with family and friends.</p>
    <div class="abs col1">
      <h3 class="heading c-title">Collection 1 [ 300 € ]</h3>
      <p class="body">Your favorite five images from the session will be professionally edited and presented to you on disk as high resolution jpegs</p>
    </div>
    <div class="abs col2">
      <h3 class="heading c-title">Collection 2 [ 400 € ]</h3>
      <p class="body">Your favorite ten images from the session will be professionally edited and given to you on disk as high resolution jpegs.<br>Your favorite image from the session will be professionally printed for you (20x30cm) on Kestrel paper, Clara's favorite for portraits.</p>
    </div>
    <div class="photo inner-photo" role="img" aria-label="Black and white photo of a child lying in the grass, resting on one hand"></div>
    <div class="band inner-band"></div>
  </article>

  <div class="abs divider"></div>

  <article class="page page--right inner-two">
    <div class="abs colA c3">
      <h3 class="heading c-title">Collection 3 [ 500 € ]</h3>
      <p class="body">Your favorite fifteen images from the session will be professionally edited and presented to you on disk as high resolution jpegs. Your favorite two images from the session will be professionally printed for you (20x30cm) on Kestrel paper, Clara's favorite for portraits.</p>
    </div>
    <div class="abs colA c4">
      <h3 class="heading c-title">Collection 4 [ 600 € ]</h3>
      <p class="body">ALL presented images from the session will be professionally edited and presented to you on disk as high resolution jpegs (approximately 40+ images). Your favorite two images from the session will be professionally printed for you 20x30cm on Kestrel paper, Clara's favorite for portraits.</p>
    </div>
    <div class="abs colA alc">
      <h3 class="heading c-title">A la carte</h3>
      <p class="body" style="margin-top:1px">These products may be purchased separately to complement your collection. A consultation with Clara will help you decide which products are best for gifts and for your home.</p>
    </div>
    <div class="abs colA alc-digital">
      <h3 class="heading item-title">A la carte - 25 € each<br>High resolution digital images</h3>
      <p class="body" style="margin-top:8px">Perfect if you just need to add "one more image" to your collection!<br>High-resolution jpeg file</p>
    </div>

    <div class="abs colB b1">
      <h3 class="heading item-title">A la carte - 25 € &nbsp;Matt prints</h3>
      <p class="body">Each print is professionally edited, printed on archival photo paper. Purchase includes the JPEG file for your personal digital use. 20x30 cm and smaller</p>
    </div>
    <div class="abs colB b2">
      <h3 class="heading item-title">A la carte - 45 € &nbsp;Kestrel prints</h3>
      <p class="body">Prints on Kestrel (watercolor) paper are Clara's favorite for large format color prints 30x40 cm</p>
    </div>
    <div class="abs colB b3">
      <h3 class="heading item-title">A la carte - 100 € &nbsp;Canvas prints</h3>
      <p class="body">Ready-to-hang, stretched canvas wall art of your favorite images 30x40 cm</p>
    </div>
    <div class="abs colB b4">
      <h3 class="heading item-title">A la carte - 350 € &nbsp;Framed + matted prints</h3>
      <p class="body">Beautiful Kestrel prints finished with wide mats and simple, elegant frames of your choice 30x40 inch</p>
    </div>
    <div class="abs colB b5">
      <h3 class="heading item-title">Prices begin at - 100 €<br>Custom designed albums</h3>
      <p class="body">Images from your session are selected for the custom design of an album and bound in a book for a modern presentation of your images. There are a number of cover choices for the classic flush-mount and beautifully crafted albums. A great way to display all of your favorite images from your session on your coffee table.</p>
    </div>
  </article>
</section>

</body>
</html>
```